KTR Photography Editing & Support Services for Real Estate

We require a double sided A4 flyer to promote our photography services to real estate agencies.
This particular service is targeted to rural areas where reliable, professional and highly skilled photographers are difficult to source. We teach the agent how to photograph, they upload files to a server and we take care of the rest (image editing, quality control and delivery). This will give the agents flexibility with when to shoot and eliminates the stress of managing a photographer / contractor. We offer a 1 day face to face training session and competitive packages for equipment start up.
We would like the flyer to look clean & very professional. The flyer should showcase samples of our work to highlight what can be achieved by using our services. We like the look of a black or dark background behind the text and feel that would look nice with our photographs provided. Otherwise open to your suggestions and ideas.
TEXT FOR FLYER:
Welcome to the KTR Real Estate Photography Editing and Support Service
• Take your real estate business to the next level by providing impressive real estate imagery that makes you stands out from the competition
• Omit the stress of trying to find a good photographer or managing an unreliable one and hence have more time to focus on other aspects of your business
• Showcase your listings with better quality and more impactful photographs than your competitors thereby increasing potential for a quick sale
• Great first impressions matter and you will achieve this by looking and feeling more professional. This will attract and retain more future clients.
HOW IT WORKS
• We understand that your time is valuable, so let us handle the editing and delivery of your images. You shoot, and we take care of the rest.
• Images are edited and delivered within 1 working day
INCLUSIONS:
• Full day face to face training (we come to you) and instructional handbook
• We will teach you everything you need to know about your equipment and how to take stunning real estate photographs
• Service turnaround within 1 working day
• Free HELP desk service Mon-Fri
• 12 month Exclusivity (rural towns only) for a limited time
INVESTMENT
• 99 per listing for us to manage images including editing, quality control and delivery (10 Images)
• Ask us about competitive packages for photography equipment if required
SUMMARY
The KTR Real Estate Photography Editing and Support Service is the perfect solution for busy real estate professionals who want to take their business to the next level. Our service is affordable, flexible, and designed to help you showcase your listings in the best possible light.
Contact us today to learn more about how we can help you.

```html
<!DOCTYPE html>
<html lang="en">
<head>
<meta charset="UTF-8">
<title>KTR Real Estate Photography Editing &amp; Support Service</title>
<link rel="stylesheet" href="https://fonts.googleapis.com/css2?family=Poppins:wght@300;400;500;600;700&family=Oswald:wght@500&display=swap">
<style>
  :root {
    --ink: #1b1b1b;
    --black: #000000;
    --paper: #ffffff;
    --grey-text: #6f6f6f;
    --price-grey: #7a7a7a;
    --panel: #8a8a8a;
    --panel-icon: #3a3a3a;
    --tick: #555555;
    --rule: #9a9a9a;
    --band: rgba(30, 30, 30, 0.78);
  }
  * { margin: 0; padding: 0; box-sizing: border-box; }
  html, body { width: 813px; height: 1200px; overflow: hidden; background: var(--paper); }
  body { font-family: "Poppins", sans-serif; color: var(--ink); }

  .sheet { position: relative; width: 813px; height: 1200px; background: var(--paper); overflow: hidden; }

  .page { position: absolute; top: 306px; width: 813px; height: 1200px; background: var(--paper); overflow: hidden;
    transform: scale(0.49); transform-origin: top left; box-shadow: 0 6px 24px rgba(0,0,0,0.25); }
  .page-front { left: 8px; }
  .page-back { left: 409px; }

  /* ---------- front ---------- */
  .brand { position: absolute; left: 40px; top: 66px; width: 340px; text-align: center; }
  .brand-name { font-size: 27px; font-weight: 300; letter-spacing: 6px; color: var(--ink); }
  .brand-role { margin-top: 10px; font-size: 13px; font-weight: 300; letter-spacing: 3.5px; color: var(--grey-text); }

  .welcome { position: absolute; left: 47px; top: 258px; line-height: 1.05; }
  .welcome-lead { font-size: 26px; font-weight: 400; color: var(--ink); }
  .welcome-title { font-size: 35px; font-weight: 700; color: var(--ink); letter-spacing: -0.3px; }
  .welcome-sub { font-size: 26px; font-weight: 300; color: var(--grey-text); }

  .hero-shadow { position: absolute; left: 434px; top: 72px; width: 332px; height: 392px; background: var(--black); }
  .hero { position: absolute; left: 407px; top: 47px; width: 333px; height: 388px; border: 4px solid var(--paper);
    background: linear-gradient(180deg, #5b7aa4 0%, #8fa0b8 35%, #3b3b40 55%, #4a5a3a 80%, #6b7a45 100%); }

  .samples { position: absolute; left: 46px; top: 426px; width: 329px; height: 361px;
    display: grid; grid-template-columns: 1fr 1fr; grid-template-rows: 1fr 1fr; gap: 6px; }
  .sample { width: 100%; height: 100%; }
  .sample-lounge { background: linear-gradient(160deg, #4a5566, #2b2f36 60%, #7a6a55); }
  .sample-bath { background: linear-gradient(180deg, #d9d2c7, #c8bdae 70%, #b9865a); }
  .sample-hall { background: linear-gradient(150deg, #8a6b4a, #d8d2c8 50%, #5a4530); }
  .sample-bedroom { background: linear-gradient(170deg, #6d8fa8, #e6e6e6 55%, #cfcfcf); }

  .how { position: absolute; left: 47px; top: 820px; width: 330px; }
  .how-title { font-size: 30px; font-weight: 400; color: var(--ink); margin-bottom: 14px; }
  .tick-list { list-style: none; }
  .tick-list li { position: relative; padding-left: 35px; font-size: 15.5px; line-height: 1.2; font-weight: 400; color: var(--ink); margin-bottom: 16px; max-width: 320px; }
  .tick-list svg { position: absolute; left: 0; top: 4px; width: 19px; height: 19px; }

  .benefits { position: absolute; left: 407px; top: 507px; width: 357px; height: 538px; background: var(--panel); padding: 34px 20px 0 20px; }
  .benefit { display: flex; gap: 18px; margin-bottom: 20px; }
  .benefit-icon { flex: 0 0 38px; width: 38px; height: 38px; margin-top: 6px; }
  .benefit p { font-size: 16px; line-height: 1.13; color: var(--paper); font-weight: 400; max-width: 245px; }

  /* ---------- shared footer ---------- */
  .footer { position: absolute; left: 0; top: 1075px; width: 813px; height: 125px; background: var(--black); }
  .portrait { position: absolute; left: 52px; top: 1017px; width: 146px; height: 146px; border-radius: 50%; border: 4px solid var(--paper);
    background: radial-gradient(circle at 50% 40%, #6b3a2c, #2a1410 75%); }
  .contact-person { position: absolute; left: 223px; top: 1097px; color: var(--paper); }
  .contact-name { font-size: 21px; font-weight: 600; color: #bdbdbd; line-height: 1; }
  .contact-role { font-size: 12.5px; font-weight: 400; color: #bdbdbd; line-height: 1.2; }
  .contact-phone { font-size: 19px; font-weight: 600; margin-top: 4px; display: flex; align-items: center; gap: 6px; }
  .contact-web { position: absolute; left: 489px; top: 1108px; color: var(--paper); }
  .contact-email { font-size: 16px; font-weight: 600; display: flex; align-items: center; gap: 10px; }
  .contact-site { font-size: 16px; font-weight: 600; letter-spacing: 1.5px; margin-top: 10px; }

  /* ---------- back ---------- */
  .cover { position: absolute; left: 0; top: 0; width: 813px; height: 521px;
    background: linear-gradient(180deg, #7b86b3 0%, #b4a9c9 28%, #d9d3cf 45%, #b08a5e 62%, #e9e6e1 80%, #cfd3d6 100%); }
  .summary { position: absolute; left: 50px; top: 319px; width: 720px; height: 184px; background: var(--band);
    padding: 34px 30px 0 33px; color: var(--paper); font-size: 20px; line-height: 1.15; font-weight: 400; }

  .coast { position: absolute; left: 50px; top: 543px; width: 330px; height: 220px;
    background: linear-gradient(180deg, #8fa2c0 0%, #e9c4b4 35%, #5f84a6 55%, #3c6a8a 68%, #5f8a3c 82%, #7aa04a 100%); }

  .investment { position: absolute; left: 407px; top: 547px; width: 370px; }
  .investment-title { font-size: 33px; font-weight: 400; line-height: 1; color: var(--ink); }
  .price { display: flex; gap: 14px; margin-top: 8px; }
  .price-figure { line-height: 0.95; }
  .price-amount { font-family: "Oswald", sans-serif; font-weight: 500; font-size: 60px; color: var(--price-grey); line-height: 1; }
  .price-unit { font-size: 42px; font-weight: 600; color: var(--ink); line-height: 0.95; }
  .price-note { font-size: 17px; line-height: 1.13; color: var(--ink); padding-top: 2px; }
  .packages { position: absolute; left: 409px; top: 700px; width: 348px; height: 64px; background: var(--black);
    color: var(--paper); font-size: 16.5px; line-height: 1.2; padding: 9px 12px 0 12px; }

  .inclusions { position: absolute; left: 47px; top: 784px; width: 713px; }
  .inclusions-head { display: flex; align-items: center; gap: 12px; }
  .inclusions-title { font-size: 31px; font-weight: 400; color: var(--ink); line-height: 1.1; }
  .inclusions-rule { flex: 1; height: 1px; background: var(--rule); margin-top: 6px; }
  .inclusion-cols { display: flex; margin-top: 26px; }
  .inclusion-col { list-style: none; }
  .inclusion-col-left { width: 400px; }
  .inclusion-col li { position: relative; padding-left: 37px; font-size: 17px; line-height: 1.15; margin-bottom: 21px; color: var(--ink); }
  .inclusion-col-right li { margin-bottom: 19px; }
  .inclusion-col svg { position: absolute; left: 0; top: 4px; width: 19px; height: 19px; }
</style>
</head>
<body>
<main class="sheet">

  <!-- front side -->
  <article class="page page-front">
    <header class="brand">
      <div class="brand-name">DANA ASHFORD</div>
      <div class="brand-role">PHOTOGRAPHER</div>
    </header>

    <section class="welcome">
      <div class="welcome-lead">WELCOME TO THE</div>
      <div class="welcome-title">KTR REAL ESTATE</div>
      <div class="welcome-sub">PHOTOGRAPHY EDITING</div>
      <div class="welcome-sub">&amp; SUPPORT SERVICE</div>
    </section>

    <div class="hero-shadow"></div>
    <div class="hero" role="img" aria-label="Dark timber cottage at dusk with lit porch and gravel garden path"></div>

    <div class="samples">
      <div class="sample sample-lounge" role="img" aria-label="Living room with dark sofa"></div>
      <div class="sample sample-bath" role="img" aria-label="Bathroom with twin basins and freestanding bath"></div>
      <div class="sample sample-hall" role="img" aria-label="Hallway with framed pictures and timber floor"></div>
      <div class="sample sample-bedroom" role="img" aria-label="Bright bedroom with view through large windows"></div>
    </div>

    <section class="how">
      <h2 class="how-title">HOW IT WORKS</h2>
      <ul class="tick-list">
        <li><svg viewBox="0 0 20 20"><circle cx="10" cy="10" r="8.5" fill="none" stroke="var(--tick)" stroke-width="1.2"/><path d="M6 10.3l2.8 2.7L14 7.5" fill="none" stroke="var(--tick)" stroke-width="1.4"/></svg>We understand that your time is valuable, so let us handle the editing and delivery of your images. You shoot, and we take care of the rest.</li>
        <li><svg viewBox="0 0 20 20"><circle cx="10" cy="10" r="8.5" fill="none" stroke="var(--tick)" stroke-width="1.2"/><path d="M6 10.3l2.8 2.7L14 7.5" fill="none" stroke="var(--tick)" stroke-width="1.4"/></svg>Images are edited and delivered<br>within 1 working day</li>
      </ul>
    </section>

    <section class="benefits">
      <div class="benefit">
        <svg class="benefit-icon" viewBox="0 0 40 40"><circle cx="20" cy="20" r="19" fill="var(--panel-icon)"/><rect x="12" y="13" width="16" height="14" rx="1.5" fill="none" stroke="#fff" stroke-width="1.4"/><path d="M13 25l5-5 4 4 2-2 4 3" fill="none" stroke="#fff" stroke-width="1.3"/><circle cx="23.5" cy="17.5" r="1.5" fill="#fff"/></svg>
        <p>Take your real estate business to the next level by providing impressive real estate imagery that makes you stands out from the competition</p>
      </div>
      <div class="benefit">
        <svg class="benefit-icon" viewBox="0 0 40 40"><circle cx="20" cy="20" r="19" fill="var(--panel-icon)"/><circle cx="20" cy="20" r="9" fill="none" stroke="#fff" stroke-width="1.4"/><circle cx="20" cy="20" r="4" fill="none" stroke="#fff" stroke-width="1.3"/><path d="M20 11l4 5M29 20l-5 4M20 29l-4-5M11 20l5-4" stroke="#fff" stroke-width="1.2"/></svg>
        <p>Omit the stress of trying to find a good photographer or managing an unreliable one and hence have more time to focus on other aspects of your business</p>
      </div>
      <div class="benefit">
        <svg class="benefit-icon" viewBox="0 0 40 40"><circle cx="20" cy="20" r="19" fill="var(--panel-icon)"/><rect x="13" y="11" width="14" height="18" rx="1.5" fill="none" stroke="#fff" stroke-width="1.4"/><path d="M16 16h8M16 20h8M16 24h8" stroke="#fff" stroke-width="1.3"/></svg>
        <p>Showcase your listings with better quality and more impactful photographs than your competitors thereby increasing potential for a quick sale</p>
      </div>
      <div class="benefit">
        <svg class="benefit-icon" viewBox="0 0 40 40"><circle cx="20" cy="20" r="19" fill="var(--panel-icon)"/><path d="M12 19h4v10h-4zM16 19l4-7c1.5 0 2.5 1 2 3l-1 3h6c1.2 0 2 1 1.8 2l-1.3 7c-.2.8-1 1.3-1.8 1.3H16" fill="none" stroke="#fff" stroke-width="1.4" stroke-linejoin="round"/></svg>
        <p>Great first impressions matter and you will achieve this by looking and feeling more professional. This will attract and retain more future clients.</p>
      </div>
    </section>

    <footer class="footer"></footer>
    <div class="portrait" role="img" aria-label="Portrait of the photographer"></div>
    <div class="contact-person">
      <div class="contact-name">DANA ASHFORD</div>
      <div class="contact-role">PHOTOGRAPHER</div>
      <div class="contact-phone">
        <svg width="15" height="15" viewBox="0 0 16 16"><path d="M3.5 1.5l2.5 0 1.2 3-1.6 1.2c.8 1.8 2.2 3.2 4 4l1.2-1.6 3 1.2v2.5c0 .8-.7 1.4-1.5 1.3C6.6 12.6 3.4 9.4 2.2 3c-.1-.8.5-1.5 1.3-1.5z" fill="#fff"/></svg>
        +61 400 555 018
      </div>
    </div>
    <div class="contact-web">
      <div class="contact-email">
        <svg width="16" height="12" viewBox="0 0 16 12"><rect x="0.7" y="0.7" width="14.6" height="10.6" fill="none" stroke="#fff" stroke-width="1.3"/><path d="M1 1l7 5.5L15 1" fill="none" stroke="#fff" stroke-width="1.3"/></svg>
        shoot@danaashford.com.au
      </div>
      <div class="contact-site">www.danaashford.com.au</div>
    </div>
  </article>

  <!-- back side -->
  <article class="page page-back">
    <div class="cover" role="img" aria-label="Modern white farmhouse with stone chimneys and lit gable windows at twilight"></div>
    <p class="summary">The KTR Real Estate Photography Editing and Support Service is the perfect solution for busy real estate professionals who want to take their business to the next level. Our service is affordable, flexible, and designed to help you showcase your listings in the best possible light.</p>

    <div class="coast" role="img" aria-label="Dark clad cabin on a clifftop above the sea at dusk"></div>

    <section class="investment">
      <h2 class="investment-title">INVESTMENT</h2>
      <div class="price">
        <div class="price-figure">
          <div class="price-amount">99 PER</div>
          <div class="price-unit">LISTING</div>
        </div>
        <p class="price-note">for us to manage<br>images including<br>editing, quality<br>control and delivery<br>(10 Images)</p>
      </div>
    </section>
    <p class="packages">Ask us about competitive packages<br>for photography equipment if required</p>

    <section class="inclusions">
      <div class="inclusions-head">
        <h2 class="inclusions-title">INCLUSIONS</h2>
        <span class="inclusions-rule"></span>
      </div>
      <div class="inclusion-cols">
        <ul class="inclusion-col inclusion-col-left">
          <li><svg viewBox="0 0 20 20"><circle cx="10" cy="10" r="8.5" fill="none" stroke="var(--tick)" stroke-width="1.2"/><path d="M6 10.3l2.8 2.7L14 7.5" fill="none" stroke="var(--tick)" stroke-width="1.4"/></svg>Full day face to face training<br>(we come to you) and<br>instructional handbook</li>
          <li><svg viewBox="0 0 20 20"><circle cx="10" cy="10" r="8.5" fill="none" stroke="var(--tick)" stroke-width="1.2"/><path d="M6 10.3l2.8 2.7L14 7.5" fill="none" stroke="var(--tick)" stroke-width="1.4"/></svg>We will teach you everything you<br>need to know about your equipment<br>and how to take stunning real<br>estate photographs</li>
        </ul>
        <ul class="inclusion-col inclusion-col-right">
          <li><svg viewBox="0 0 20 20"><circle cx="10" cy="10" r="8.5" fill="none" stroke="var(--tick)" stroke-width="1.2"/><path d="M6 10.3l2.8 2.7L14 7.5" fill="none" stroke="var(--tick)" stroke-width="1.4"/></svg>Service turnaround within<br>1 working day</li>
          <li><svg viewBox="0 0 20 20"><circle cx="10" cy="10" r="8.5" fill="none" stroke="var(--tick)" stroke-width="1.2"/><path d="M6 10.3l2.8 2.7L14 7.5" fill="none" stroke="var(--tick)" stroke-width="1.4"/></svg>Free HELP desk service<br>Mon-Fri</li>
          <li><svg viewBox="0 0 20 20"><circle cx="10" cy="10" r="8.5" fill="none" stroke="var(--tick)" stroke-width="1.2"/><path d="M6 10.3l2.8 2.7L14 7.5" fill="none" stroke="var(--tick)" stroke-width="1.4"/></svg>12 month Exclusivity<br>(rural towns only) for a limited time</li>
        </ul>
      </div>
    </section>

    <footer class="footer"></footer>
    <div class="portrait" role="img" aria-label="Portrait of the photographer"></div>
    <div class="contact-person">
      <div class="contact-name">DANA ASHFORD</div>
      <div class="contact-role">PHOTOGRAPHER</div>
      <div class="contact-phone">
        <svg width="15" height="15" viewBox="0 0 16 16"><path d="M3.5 1.5l2.5 0 1.2 3-1.6 1.2c.8 1.8 2.2 3.2 4 4l1.2-1.6 3 1.2v2.5c0 .8-.7 1.4-1.5 1.3C6.6 12.6 3.4 9.4 2.2 3c-.1-.8.5-1.5 1.3-1.5z" fill="#fff"/></svg>
        +61 400 555 018
      </div>
    </div>
    <div class="contact-web">
      <div class="contact-email">
        <svg width="16" height="12" viewBox="0 0 16 12"><rect x="0.7" y="0.7" width="14.6" height="10.6" fill="none" stroke="#fff" stroke-width="1.3"/><path d="M1 1l7 5.5L15 1" fill="none" stroke="#fff" stroke-width="1.3"/></svg>
        shoot@danaashford.com.au
      </div>
      <div class="contact-site">www.danaashford.com.au</div>
    </div>
  </article>

</main>
</body>
</html>
```